Specialised investor in e-mobility and energy wants business card design

We need a business card design that fits our existing corporate design. <The look and feel must be 'sharp'/'clean', dynamic, communicate momentum, professionalism etc (as one would imagine from a firm in the financial sector). We like the idea of a reverse-side of the card that includes the logo, and the name and contact details on the other. We expect the deliverable to be whatever format might be required to be able to get cards printed directly by a service such as kelmo press. Our website is www.zub.capital

```html
<!DOCTYPE html>
<html lang="en">
<head>
<meta charset="utf-8">
<title>ZUB Capital – Business Card</title>
<link rel="stylesheet" href="https://fonts.googleapis.com/css2?family=Montserrat:wght@400;500;700&display=swap">
<style>
  :root {
    --green-dark: #2c5a25;
    --green-light: #7cb449;
    --ink: #2b2b2b;
    --card: #ffffff;
    --backdrop: #e9e6e1;
  }
  * { margin: 0; padding: 0; box-sizing: border-box; }
  html, body {
    width: 1200px; height: 960px; overflow: hidden;
    background: var(--backdrop);
    font-family: "Montserrat", sans-serif;
  }
  .sheet {
    width: 1200px; height: 960px;
    display: flex; flex-direction: column; align-items: center; justify-content: center;
    gap: 40px;
  }
  .card {
    position: relative;
    width: 700px; height: 400px;
    background: var(--card);
    border-radius: 36px;
    box-shadow: 0 6px 18px rgba(0,0,0,0.12);
    overflow: hidden;
  }
  .brand {
    display: flex; align-items: center; gap: 16px;
    color: var(--green-dark);
    font-weight: 500;
    letter-spacing: 1px;
  }
  .brand-dot {
    width: 22px; height: 22px; border-radius: 50%;
    background: var(--green-dark);
  }
  .card-front .brand {
    position: absolute; left: 0; right: 0; top: 0; bottom: 0;
    justify-content: center;
    font-size: 72px;
  }
  .card-back .brand {
    position: absolute; left: 0; right: 0; top: 58px;
    justify-content: center;
    font-size: 58px;
  }
  .card-back .brand-dot { width: 18px; height: 18px; }
  .details {
    position: absolute; top: 180px; left: 0; right: 0;
    display: flex; justify-content: center; align-items: center; gap: 24px;
  }
  .person { text-align: right; }
  .person-name {
    color: var(--green-light);
    font-weight: 700; font-size: 26px; letter-spacing: 0.5px;
    text-transform: uppercase;
  }
  .person-role {
    color: var(--ink); font-size: 18px; margin-top: 2px;
  }
  .divider {
    width: 2px; height: 74px; background: var(--green-light);
  }
  .contacts { list-style: none; }
  .contacts li {
    display: flex; align-items: center; gap: 10px;
    color: var(--ink); font-size: 17px; line-height: 26px;
  }
  .contacts svg { width: 15px; height: 15px; fill: var(--green-dark); flex: none; }
  .address-band {
    position: absolute; left: 0; right: 0; bottom: 34px; height: 40px;
    background: var(--green-dark);
    color: #fff;
    font-size: 17px; letter-spacing: 0.5px;
    display: flex; align-items: center; justify-content: center;
  }
</style>
</head>
<body>
<main class="sheet">

  <section class="card card-front" aria-label="Card front">
    <div class="brand"><span class="brand-dot"></span><span class="brand-name">ZUB Capital</span></div>
  </section>

  <section class="card card-back" aria-label="Card back">
    <div class="brand"><span class="brand-dot"></span><span class="brand-name">ZUB Capital</span></div>

    <div class="details">
      <div class="person">
        <p class="person-name">Marcus Ellery</p>
        <p class="person-role">Managing Director</p>
      </div>
      <span class="divider"></span>
      <ul class="contacts">
        <li>
          <svg viewBox="0 0 16 16" aria-hidden="true"><path d="M2 5c0-2 1.5-3 6-3s6 1 6 3v1h-3V5H5v1H2z M4 7h8l2 6H2z"/></svg>
          +41 79555 0148
        </li>
        <li>
          <svg viewBox="0 0 16 16" aria-hidden="true"><path d="M1 4h14v1L8 9 1 5z M1 6.5l7 4 7-4V12H1z"/></svg>
          marcus@zub.capital
        </li>
        <li>
          <svg viewBox="0 0 16 16" aria-hidden="true"><circle cx="8" cy="8" r="7"/></svg>
          www.zub.capital
        </li>
      </ul>
    </div>

    <div class="address-band">ZUB Capital S.A. Geneva, Switzerland</div>
  </section>

</main>
</body>
</html>
```